Dunmore Roofing

Want a professional looking business card

Industry/Entity Type

Business

Contact Information for Business Card

Paul Dunmore ( Owner) paul@dunmoreroofing-example.com, www.dunmoreroofing-example.com, Adress: 4172 Township road 43 Harlow Creek,HC K9X4T2

```html
<!DOCTYPE html>
<html lang="en">
<head>
<meta charset="utf-8">
<title>Dunmore Roofing – Business Card</title>
<link rel="stylesheet" href="https://fonts.googleapis.com/css2?family=Roboto:wght@300;400;500;700&family=Roboto+Condensed:wght@400;700&display=swap">
<style>
  :root {
    --page-bg: #ece9e4;
    --card-white: #ffffff;
    --card-fade: #eeeeee;
    --brand-blue: #1b5cb5;
    --brand-blue-deep: #0f4294;
    --brand-blue-light: #2a6ccc;
    --rule-grey: #b9bec6;
    --band-grey: #6b6e72;
    --text-muted: #6f7a89;
    --white: #ffffff;
  }
  * { box-sizing: border-box; margin: 0; padding: 0; }
  html, body { width: 1200px; height: 780px; overflow: hidden; }
  body {
    background: var(--page-bg);
    font-family: "Roboto", Arial, sans-serif;
    display: flex;
    align-items: center;
    justify-content: center;
    gap: 48px;
  }
  .card {
    position: relative;
    width: 540px;
    height: 310px;
    border-radius: 18px;
    overflow: hidden;
    box-shadow: 0 10px 26px rgba(0,0,0,.18);
  }

  /* Front */
  .card-front {
    background: radial-gradient(ellipse at 30% 40%, var(--card-white) 40%, var(--card-fade) 100%);
  }
  .front-brand {
    position: absolute;
    left: 40px;
    top: 78px;
    width: 250px;
  }
  .brand-row { display: flex; align-items: center; gap: 12px; }
  .brand-square {
    width: 34px; height: 34px;
    background: var(--brand-blue);
    flex: none;
  }
  .brand-name {
    font-family: "Roboto Condensed", Arial, sans-serif;
    font-weight: 700;
    color: var(--brand-blue);
    font-size: 30px;
    line-height: 1;
    letter-spacing: 1px;
    text-transform: uppercase;
  }
  .brand-name .brand-sub {
    display: block;
    font-size: 14px;
    letter-spacing: 11px;
    margin-top: 6px;
  }
  .front-web {
    margin-top: 14px;
    font-size: 12px;
    color: var(--text-muted);
    letter-spacing: .4px;
  }
  .front-contact {
    position: absolute;
    left: 310px;
    top: 48px;
    width: 210px;
  }
  .person-name {
    font-family: "Roboto Condensed", Arial, sans-serif;
    color: var(--brand-blue);
    font-size: 22px;
    text-align: center;
  }
  .person-role {
    font-size: 11px;
    color: var(--text-muted);
    text-align: center;
    margin-top: 1px;
  }
  .contact-rule {
    height: 1px;
    background: var(--rule-grey);
    margin: 12px 0 10px;
  }
  .contact-line {
    display: flex;
    align-items: center;
    gap: 8px;
    font-size: 11.5px;
    color: var(--text-muted);
    white-space: nowrap;
  }
  .contact-icon {
    width: 16px; height: 16px;
    flex: none;
    background: var(--brand-blue);
    border-radius: 2px;
    display: flex; align-items: center; justify-content: center;
  }
  .address-band {
    position: absolute;
    left: 0; right: 0; bottom: 0;
    height: 44px;
    background: var(--brand-blue);
    border-top: 6px solid var(--rule-grey);
    color: var(--white);
    font-size: 14px;
    letter-spacing: .3px;
    display: flex; align-items: center; justify-content: center;
  }

  /* Back */
  .card-back {
    background: radial-gradient(ellipse at 55% 40%, var(--brand-blue-light) 0%, var(--brand-blue) 45%, var(--brand-blue-deep) 100%);
  }
  .back-brand {
    position: absolute;
    left: 0; right: 0; top: 96px;
    display: flex; justify-content: center;
  }
  .back-brand .brand-square { background: var(--white); width: 44px; height: 44px; }
  .back-brand .brand-name { color: var(--white); font-size: 40px; }
  .back-brand .brand-name .brand-sub { font-size: 17px; letter-spacing: 15px; }
  .hours-band {
    position: absolute;
    left: 0; right: 0; bottom: 0;
    height: 40px;
    background: var(--band-grey);
    border-top: 3px solid var(--white);
    color: var(--white);
    font-size: 13px;
    display: flex; align-items: center; justify-content: center;
    white-space: nowrap;
  }
  .hours-band b { font-weight: 700; }
</style>
</head>
<body>

  <section class="card card-front">
    <div class="front-brand">
      <div class="brand-row">
        <span class="brand-square"></span>
        <span class="brand-name">Dunmore<span class="brand-sub">Roofing</span></span>
      </div>
      <p class="front-web">www.dunmoreroofing-example.com</p>
    </div>

    <div class="front-contact">
      <p class="person-name">Paul Dunmore</p>
      <p class="person-role">Owner</p>
      <div class="contact-rule"></div>
      <p class="contact-line">
        <span class="contact-icon">
          <svg width="10" height="10" viewBox="0 0 24 24"><path fill="#fff" d="M6.6 10.8a15.2 15.2 0 0 0 6.6 6.6l2.2-2.2a1 1 0 0 1 1-.25 11.4 11.4 0 0 0 3.6.6 1 1 0 0 1 1 1V20a1 1 0 0 1-1 1A17 17 0 0 1 3 4a1 1 0 0 1 1-1h3.5a1 1 0 0 1 1 1c0 1.25.2 2.45.6 3.6a1 1 0 0 1-.25 1z"/></svg>
        </span>
        (613) 555-0148
      </p>
      <div class="contact-rule"></div>
      <p class="contact-line">
        <span class="contact-icon">
          <svg width="11" height="9" viewBox="0 0 22 16"><rect x="1" y="1" width="20" height="14" fill="none" stroke="#fff" stroke-width="2"/><path d="M1 1l10 8 10-8" fill="none" stroke="#fff" stroke-width="2"/></svg>
        </span>
        paul@dunmoreroofing-example.com
      </p>
    </div>

    <div class="address-band">4172 Township road 43, Harlow Creek, HC K9X4T2</div>
  </section>

  <section class="card card-back">
    <div class="back-brand">
      <div class="brand-row">
        <span class="brand-square"></span>
        <span class="brand-name">Dunmore<span class="brand-sub">Roofing</span></span>
      </div>
    </div>
    <div class="hours-band">
      <span><b>Monday - Friday</b> : 9am - 5pm | <b>Saturday</b> : By appointment | <b>Sunday</b> : Closed</span>
    </div>
  </section>

</body>
</html>
```